Truck Outfitters and Trailer Hitch Retailer Website

We are working with a hitch installer in California called Brisk Tow. They sell and install trailer hitches, bedliners for trucks, and pickup truck accessories.
Some sites to use for content/competitors:
https://www.varlomi.com/pick-up-outfitters
https://bramwells-rigs.com
https://www.thetowlodge.com
https://towlodgeinccom.quenrivsites.com
Some sites to use for inspiration:
https://www.ironmarkcouplers.com
https://quietcouplers.com
https://velmatow.com/
https://www.harborcoat.com
https://www.rugged-trailpath.com
Thank you for taking the time to consider designing a website for us. We are web developers based in Stockton, CA, USA. Most of our projects go through the same process. Understanding this process may help you win a project with us. We custom-code all of our websites in-house. We don’t have any requirements as to what tools you use for your design, but we prefer Figma files. For any design that we label as four-stars, we send it to the client for review. The client picks the final design they want us to use. Once we complete this process, we will continue to show additional clients all the four-star sites and purchase them later. Your designs will have multiple chances to sell. For better chances of success, we ask that you follow these guidelines.
IMAGES:
If you use any images or icons in the design, we ask that you have a link to the asset so we can purchase the image/icon. Most of the designs we submit do not have the customer’s images on them unless they have some great images. Be creative; show us the feeling you are trying to portray with your image choices. Use any royalty-free site you choose. We subscribe to Adobe and mainly use their images, but we can purchase images outside of Adobe.
PLEASE NOTE: we will not submit designs to clients with watermarks on the images.
FONTS:
We ask that you identify the fonts used in the design. This can be done in a message if you want. We typically use Google Fonts and Adobe Fonts.
CONTENT:
We're always open to different content and ideas. We often submit designs with stock images so the client can see our vision. We typically take pictures after the website launch to use their images with our vision. Lorem Ipsum is fine for paragraphs, but we ask that you write the headers in correct English. We want to be able to show the vision and identify the sections of the website.
INSPIRATION:
We typically add a couple of links in the brief of websites we like to help you get started in your design.
REVISIONS:
We do not often ask for revisions of the designs unless we see something in the design that may not appeal to the client. If there are slight changes that we want to make, we do that in the development process.
FEEDBACK:
We rarely give feedback on designs during the design process. We are working on many website projects and do not have the time to provide feedback. We usually respond if your request is well thought out and asks specific questions, but a note asking “feedback, please” usually goes unanswered
Number of Pages Required
1 page
Look and feel
Each slider illustrates characteristics of the customer's brand and the style your logo design should communicate.

```html
<!DOCTYPE html>
<html lang="en">
<head>
<meta charset="utf-8">
<title>Brisk Tow – Trailer Hitches, Bedliners &amp; Truck Accessories</title>
<link rel="stylesheet" href="https://fonts.googleapis.com/css2?family=Audiowide&family=Roboto:wght@400;500;700&display=swap">
<style>
:root{
  --red:#e3151a;
  --red-dark:#b90f13;
  --black:#000;
  --panel:#0f0f0f;
  --card:#1a1a1a;
  --gray:#5c5c5c;
  --head-gray:#8c8c8c;
  --text:#c9c9c9;
  --muted:#9a9a9a;
  --white:#fff;
  --gold:#f5b400;
}
*{box-sizing:border-box;margin:0;padding:0}
html,body{width:1200px;height:4505px;overflow:hidden}
body{position:relative;background:var(--black);font-family:'Roboto',sans-serif;color:var(--text)}
.abs{position:absolute}
.display{font-family:'Audiowide',sans-serif;text-transform:uppercase;letter-spacing:1px}
.eyebrow{position:absolute;font-weight:700;font-size:18px;color:var(--red);text-transform:uppercase;letter-spacing:.5px}
.section-title{position:absolute;left:0;width:1200px;text-align:center;font-size:37px;color:var(--head-gray)}
.center{left:0;width:1200px;text-align:center}
.vline{position:absolute;left:599px;width:2px;background:#555}
.vline::after{content:"";position:absolute;bottom:-4px;left:-3px;width:8px;height:8px;border-radius:50%;background:#666}

.btn{position:absolute;height:50px;display:flex;align-items:center;font-weight:700;font-size:16px;color:var(--white);text-transform:uppercase}
.btn .btn-face{background:var(--gray);height:100%;display:flex;align-items:center;padding:0 24px;clip-path:polygon(0 0,100% 0,92% 100%,0 100%)}
.btn svg{margin-left:-14px}

.nav{position:absolute;top:0;left:0;width:1200px;height:91px;background:#000}
.nav a{position:absolute;top:36px;font-size:15px;color:var(--muted);text-decoration:none}
.nav a.active{color:var(--red)}
.brand{position:absolute;top:78px;left:500px;width:200px;text-align:center}
.brand-name{font-family:'Audiowide',sans-serif;font-size:20px;color:var(--head-gray);line-height:1}

.hero{position:absolute;top:91px;left:0;width:1200px;height:670px;background:linear-gradient(100deg,#2a2a28 0%,#4a4a44 35%,#6c6a60 60%,#5f7060 85%,#2e3a2e 100%)}
.hero-shade{position:absolute;inset:0;background:linear-gradient(90deg,rgba(0,0,0,.7) 0%,rgba(0,0,0,.2) 55%,rgba(0,0,0,0) 100%)}

.service{position:absolute;top:1521px;width:313px;height:300px;border:1px solid #222;overflow:hidden}
.service .ph{position:absolute;inset:0}
.service .ph::after{content:"";position:absolute;inset:0;background:linear-gradient(180deg,rgba(0,0,0,0) 45%,rgba(0,0,0,.85) 100%)}
.service h3{position:absolute;left:0;right:0;bottom:28px;text-align:center;font-size:21px;font-weight:700;color:var(--white);text-transform:uppercase;z-index:1}
.service.featured{background:var(--red)}
.service.featured h3{top:96px;bottom:auto}
.service.featured p{position:absolute;top:140px;left:32px;right:32px;text-align:center;font-size:12px;line-height:21px;color:var(--white)}

.feature{position:absolute;left:112px;width:500px}
.feature .icon{position:absolute;left:0;top:0;width:62px;height:62px;border-radius:50%;background:var(--red);display:flex;align-items:center;justify-content:center}
.feature h4{position:absolute;left:86px;top:0;font-size:17px;color:var(--white);font-weight:700;white-space:nowrap}
.feature p{position:absolute;left:86px;top:30px;width:440px;font-size:13.5px;line-height:23px;color:var(--muted)}

.post{position:absolute;top:2643px;width:313px;height:330px}
.post .ph{position:absolute;left:0;top:0;width:313px;height:251px}
.post .box{position:absolute;left:21px;top:187px;width:270px;height:129px;background:var(--gray);text-align:center;padding:18px 16px 0}
.post.featured .box{background:var(--red)}
.post h5{font-size:15px;font-weight:500;color:var(--white);line-height:20px}
.post p{font-size:12.5px;line-height:20px;color:#eee;margin-top:10px}
.post .go{position:absolute;left:138px;top:300px;width:36px;height:36px;border-radius:50%;background:var(--red);display:flex;align-items:center;justify-content:center}
.post.featured .go{background:#6a6a6a}

.review{position:absolute;top:3257px;height:232px;background:#141414;border-radius:30px}
.review .avatar{position:absolute;left:12px;top:59px;width:116px;height:116px;border-radius:50%;background:radial-gradient(circle at 50% 40%,#8a8a8a,#3d3d3d 70%)}
.review .quote{position:absolute;left:160px;top:20px;font-family:Georgia,serif;font-size:64px;color:var(--red);line-height:1;font-style:italic;font-weight:700}
.review p{position:absolute;left:166px;top:75px;width:280px;font-size:14px;line-height:23px;color:var(--muted)}
.review h6{position:absolute;left:166px;top:165px;font-size:16px;font-weight:700;color:var(--white)}
.review .stars{position:absolute;left:166px;top:187px;color:var(--gold);font-size:17px;letter-spacing:1px}

.field{position:absolute;border:1px solid #4a4a4a;background:rgba(0,0,0,.25);font-size:12px;color:#888;padding:12px 14px}

.foot-links{position:absolute;left:544px;top:4282px;list-style:none}
.foot-links li{font-size:14px;line-height:22.4px;color:var(--muted)}
.info{position:absolute;left:824px;font-size:14px;color:var(--muted);display:flex;align-items:center;gap:12px}
.social{display:inline-block;width:30px;height:30px;border-radius:50%;border:1px solid #777;margin:0 4px}
</style>
</head>
<body>

<header class="nav">
  <a class="active" style="left:112px">Home</a>
  <a style="left:175px">About</a>
  <a style="left:240px">Our Services</a>
  <a style="left:350px">Our Products</a>
  <a style="left:745px">Gallery</a>
  <a style="left:815px">Become A Dealer</a>
  <a style="left:957px">Contact</a>
  <svg class="abs" style="left:1038px;top:36px" width="18" height="18" viewBox="0 0 18 18"><circle cx="7.5" cy="7.5" r="5.5" fill="none" stroke="#888" stroke-width="1.8"/><line x1="11.5" y1="11.5" x2="16" y2="16" stroke="#888" stroke-width="1.8"/></svg>
  <svg class="abs" style="left:1068px;top:35px" width="22" height="20" viewBox="0 0 22 20"><path d="M1 2h4l2.5 11h11L21 5H6" fill="none" stroke="#888" stroke-width="1.8"/><circle cx="9" cy="17" r="1.7" fill="#888"/><circle cx="17" cy="17" r="1.7" fill="#888"/></svg>
</header>

<section class="hero" role="img" aria-label="Photo of a hand coupling a trailer hitch to the tow ball of a truck">
  <div class="hero-shade"></div>
</section>
<div class="brand">
  <div class="brand-name">BRISK TOW</div>
</div>
<div class="eyebrow" style="left:112px;top:249px">Brisk Tow</div>
<h1 class="abs display" style="left:112px;top:284px;font-size:40px;line-height:52px;color:var(--white);font-weight:400">Ready to haul<br>any load</h1>
<div class="btn" style="left:112px;top:425px">
  <span class="btn-face" style="width:172px">Get Started</span>
  <svg width="38" height="50" viewBox="0 0 38 50"><polygon points="10,0 18,0 36,50 28,50" fill="var(--red)"/><polygon points="20,0 24,0 38,44 36,50" fill="var(--red)"/></svg>
</div>
<div class="abs" style="left:563px;top:647px;width:22px;height:4px;background:var(--red)"></div>
<div class="abs" style="left:589px;top:647px;width:22px;height:4px;background:#aaa"></div>
<div class="abs" style="left:615px;top:647px;width:22px;height:4px;background:#aaa"></div>
<svg class="abs" style="left:0;top:600px" width="1200" height="170" viewBox="0 0 1200 170">
  <polygon points="0,25 600,120 1200,25 1200,170 0,170" fill="#000"/>
  <polygon points="70,60 600,140 1130,60 1140,72 600,152 60,72" fill="var(--red)"/>
</svg>

<div class="abs display" style="left:105px;top:1000px;width:420px;text-align:center;font-size:54px;color:#3a3a3a">Brisk Tow</div>
<div class="eyebrow" style="left:643px;top:822px">About Us</div>
<h2 class="abs display" style="left:643px;top:860px;font-size:37px;line-height:46px;color:var(--head-gray);font-weight:400">We do sale &amp;<br><span style="color:var(--red)">Installation</span></h2>
<p class="abs" style="left:643px;top:978px;width:445px;font-size:13.5px;line-height:25.5px;color:var(--muted);text-align:justify">Lorem ipsum dolor sit amet, consectetur adipiscing elit, sed do eiusmod tempor incididunt ut labore et dolore magna aliqua. Ut enim ad minim veniam, quis nostrud exercitation ullamco laboris nisi ut aliquip ex ea commodo consequat.</p>
<p class="abs" style="left:643px;top:1098px;width:445px;font-size:13.5px;line-height:25.5px;color:var(--muted);text-align:justify">Duis aute irure dolor in reprehenderit in voluptate velit esse cillum dolore eu fugiat nulla pariatur. Excepteur sint occaecat cupidatat non culpa qui officia deserunt mollit anim id est laborum.</p>
<div class="btn" style="left:643px;top:1210px">
  <span class="btn-face" style="width:158px">Learn More</span>
  <svg width="38" height="50" viewBox="0 0 38 50"><polygon points="10,0 18,0 36,50 28,50" fill="var(--red)"/><polygon points="20,0 24,0 38,44 36,50" fill="var(--red)"/></svg>
</div>

<div class="vline" style="top:1329px;height:58px"></div>
<div class="eyebrow center" style="top:1407px">What we do</div>
<h2 class="section-title display" style="top:1435px;font-weight:400">Our Services</h2>

<article class="service" style="left:112px">
  <div class="ph" role="img" aria-label="Photo of a trailer hitch coupler being locked" style="background:linear-gradient(160deg,#6c6f66,#3e4039 60%,#2a2b27)"></div>
  <h3>Trailer Hitches</h3>
</article>
<article class="service featured" style="left:443px">
  <h3>Bedliners for Trucks</h3>
  <p>Lorem ipsum dolor sit amet, consectetur adipiscing elit, do eiusmod tempor incididunt ut labore et dolore magna aliqua.</p>
  <svg class="abs" style="left:139px;top:232px" width="36" height="36" viewBox="0 0 36 36"><circle cx="18" cy="18" r="16" fill="#fff"/><path d="M11 18h13M19 12l6 6-6 6" fill="none" stroke="var(--red)" stroke-width="2.4"/></svg>
</article>
<article class="service" style="left:775px">
  <div class="ph" role="img" aria-label="Photo of a trailer coupler on grass" style="background:linear-gradient(160deg,#707468,#4f5a3e 55%,#2b2f24)"></div>
  <h3>Truck Accessories</h3>
</article>

<svg class="abs" style="left:0;top:1854px" width="1200" height="640" viewBox="0 0 1200 640">
  <polygon points="0,0 600,70 1200,0 1200,560 600,630 0,560" fill="var(--panel)"/>
</svg>
<div class="vline" style="top:1938px;height:56px"></div>
<div class="eyebrow" style="left:112px;top:2011px">Features &amp; Benefits</div>
<h2 class="abs display" style="left:112px;top:2038px;font-size:37px;color:var(--head-gray);font-weight:400">Why choose us</h2>

<div class="feature" style="top:2123px">
  <div class="icon"><svg width="30" height="30" viewBox="0 0 30 30" fill="none" stroke="#fff" stroke-width="1.8"><rect x="5" y="13" width="20" height="13"/><rect x="3" y="9" width="24" height="5"/><path d="M15 9v17M15 9c-3-5-8-4-6-1 1 1 4 1 6 1 2 0 5 0 6-1 2-3-3-4-6 1"/></svg></div>
  <h4>Professional Customer Service</h4>
  <p>Lorem ipsum dolor sit amet, consectetur adipiscing elit, sed incididunt ut labore et dolore magna aliqua.</p>
</div>
<div class="feature" style="top:2228px">
  <div class="icon"><svg width="30" height="30" viewBox="0 0 30 30" fill="none" stroke="#fff" stroke-width="1.8"><circle cx="15" cy="11" r="7"/><path d="M12 11l2 2 4-4M4 18c3 0 5 2 7 4h6c2-2 4-4 7-4"/><path d="M3 26h24"/></svg></div>
  <h4>Committed to Quality</h4>
  <p>Sed ut perspiciatis unde omnis iste natus error sit voluptatem accusantium doloremque laudantium,</p>
</div>
<div class="feature" style="top:2328px">
  <div class="icon"><svg width="30" height="30" viewBox="0 0 30 30" fill="none" stroke="#fff" stroke-width="1.8"><path d="M15 3l10 4v7c0 7-5 11-10 13C10 25 5 21 5 14V7z"/><path d="M10 15l3 3 7-7"/></svg></div>
  <h4>Lifetime Warranty</h4>
  <p>At vero eos et accusamus et iusto odio dignissimos ducimus praesentium voluptatum deleniti corrupti quos dolores</p>
</div>

<div class="abs" role="img" aria-label="Photo of a hand lifting a trailer coupler" style="left:700px;top:2001px;width:342px;height:365px;background:linear-gradient(150deg,#2f4a8a 0%,#4f6d3a 35%,#8f948c 70%,#5b5f5a 100%);clip-path:polygon(0 0,100% 0,100% 100%,25% 100%)"></div>
<div class="abs" role="img" aria-label="Photo of a ribbed truck bedliner" style="left:686px;top:2215px;width:130px;height:192px;background:linear-gradient(160deg,#3a3a3a,#161616);clip-path:polygon(0 0,80% 0,100% 100%,0 100%)"></div>
<svg class="abs" style="left:745px;top:2053px" width="345" height="370" viewBox="0 0 345 370"><polygon points="5,5 342,5 342,366 90,366" fill="none" stroke="var(--red)" stroke-width="6"/></svg>

<div class="vline" style="top:2440px;height:68px"></div>
<div class="eyebrow center" style="top:2528px">Recent Update</div>
<h2 class="section-title display" style="top:2558px;font-weight:400">Our Blog Post</h2>

<article class="post" style="left:112px">
  <div class="ph" role="img" aria-label="Photo of a tow ball mount on a truck" style="background:linear-gradient(160deg,#8c8c86,#3a3a36)"></div>
  <div class="box"><h5>Lorem ipsum , consectetur adipiscing elit</h5><p>Sed ut perspiciatis unde omnis iste natus error sit voluptatem</p></div>
  <div class="go"><svg width="18" height="18" viewBox="0 0 18 18"><path d="M3 9h11M10 5l4 4-4 4" fill="none" stroke="#fff" stroke-width="2"/></svg></div>
</article>
<article class="post featured" style="left:443px">
  <div class="ph" role="img" aria-label="Photo of a pickup truck bed with bedliner" style="background:linear-gradient(180deg,#4a3a24,#2b3440 45%,#1a2028)"></div>
  <div class="box"><h5>Lorem ipsum , consectetur adipiscing elit</h5><p>Sed ut perspiciatis unde omnis iste natus error sit voluptatem</p></div>
  <div class="go"><svg width="18" height="18" viewBox="0 0 18 18"><path d="M3 9h11M10 5l4 4-4 4" fill="none" stroke="#fff" stroke-width="2"/></svg></div>
</article>
<article class="post" style="left:775px">
  <div class="ph" role="img" aria-label="Photo of a galvanised trailer coupler" style="background:linear-gradient(160deg,#9b9c94,#6a6a60 50%,#4a4840)"></div>
  <div class="box"><h5>Lorem ipsum , consectetur adipiscing elit</h5><p>Sed ut perspiciatis unde omnis iste natus error sit voluptatem</p></div>
  <div class="go"><svg width="18" height="18" viewBox="0 0 18 18"><path d="M3 9h11M10 5l4 4-4 4" fill="none" stroke="#fff" stroke-width="2"/></svg></div>
</article>

<div class="vline" style="top:3043px;height:68px"></div>
<div class="eyebrow center" style="top:3136px">Testimonials</div>
<h2 class="section-title display" style="top:3167px;font-weight:400">What our clients say</h2>

<svg class="abs" style="left:42px;top:3356px" width="24" height="34" viewBox="0 0 24 34"><path d="M19 3L5 17l14 14" fill="none" stroke="#ccc" stroke-width="4"/></svg>
<svg class="abs" style="left:1134px;top:3356px" width="24" height="34" viewBox="0 0 24 34"><path d="M5 3l14 14L5 31" fill="none" stroke="#ccc" stroke-width="4"/></svg>

<article class="review" style="left:114px;width:472px">
  <div class="avatar" role="img" aria-label="Client portrait"></div>
  <div class="quote">“</div>
  <p>Sed ut perspiciatis unde omnis iste natus sit voluptatem accusantium doloremque laudantium, totam rem aperiam,</p>
  <h6>John Doe</h6>
  <div class="stars">★★★★★</div>
</article>
<article class="review" style="left:666px;width:408px">
  <div class="avatar" role="img" aria-label="Client portrait"></div>
  <div class="quote">“</div>
  <p>Sed ut perspiciatis unde omnis iste natus sit voluptatem accusantium doloremque laudantium, totam rem aperiam,</p>
  <h6>John Doe</h6>
  <div class="stars">★★★★★</div>
</article>

<div class="abs" role="img" aria-label="Dark photo of a city skyline" style="left:0;top:3547px;width:1200px;height:616px;background:linear-gradient(180deg,#121212 0%,#1f1f1f 40%,#141414 100%)"></div>
<div class="vline" style="top:3617px;height:70px"></div>
<div class="eyebrow center" style="top:3712px">Contact Us</div>
<h2 class="section-title display" style="top:3740px;font-weight:400">Get in touch</h2>
<div class="field" style="left:269px;top:3813px;width:322px;height:40px">First Name</div>
<div class="field" style="left:607px;top:3813px;width:322px;height:40px">Last Name</div>
<div class="field" style="left:269px;top:3872px;width:322px;height:42px">Email Address</div>
<div class="field" style="left:607px;top:3872px;width:322px;height:42px">Phone Number</div>
<div class="field" style="left:269px;top:3932px;width:660px;height:73px">Message</div>
<div class="btn" style="left:507px;top:4047px;height:47px">
  <span class="btn-face" style="width:147px;font-size:15px">Submit Now</span>
  <svg width="38" height="47" viewBox="0 0 38 50"><polygon points="10,0 18,0 36,50 28,50" fill="var(--red)"/><polygon points="20,0 24,0 38,44 36,50" fill="var(--red)"/></svg>
</div>

<footer>
  <div class="abs display" style="left:104px;top:4320px;width:300px;text-align:center;font-size:26px;color:var(--head-gray)">Brisk Tow</div>
  <div class="abs" style="left:196px;top:4375px;width:120px;text-align:center">
    <span class="social"></span><span class="social" style="background:var(--red);border-color:var(--red)"></span><span class="social"></span>
  </div>

  <div class="abs" style="left:447px;top:4233px;width:4px;height:44px;background:var(--red)"></div>
  <div class="abs" style="left:734px;top:4233px;width:4px;height:44px;background:var(--red)"></div>

  <h4 class="abs" style="left:544px;top:4232px;font-size:15px;font-weight:700;color:var(--white)">QUICK LINKS</h4>
  <ul class="foot-links">
    <li>Home</li><li>About</li><li>Our Services</li><li>Our Products</li><li>Gallery</li><li>Contact</li>
  </ul>

  <h4 class="abs" style="left:824px;top:4232px;font-size:15px;font-weight:700;color:var(--white)">CONTACT INFO</h4>
  <div class="info" style="top:4276px"><svg width="16" height="18" viewBox="0 0 16 18"><path d="M8 17s6-6 6-10A6 6 0 0 0 2 7c0 4 6 10 6 10z" fill="var(--red)"/><circle cx="8" cy="7" r="2" fill="#000"/></svg>2145 Alder Lane, San Jose, CA</div>
  <div class="info" style="top:4314px"><svg width="16" height="16" viewBox="0 0 16 16"><path d="M3 1l3 3-2 2c1 2 3 4 5 5l2-2 3 3-2 3C7 15 1 9 1 3z" fill="var(--red)"/></svg>+1 888 888 8888</div>
  <div class="info" style="top:4351px"><svg width="16" height="16" viewBox="0 0 16 16"><rect x="3" y="1" width="10" height="5" fill="none" stroke="var(--red)" stroke-width="1.5"/><rect x="1" y="6" width="14" height="7" rx="1" fill="var(--red)"/><rect x="4" y="10" width="8" height="5" fill="#000" stroke="var(--red)"/></svg>Fax. 123 456 7890</div>
  <div class="info" style="top:4388px"><svg width="16" height="13" viewBox="0 0 16 13"><rect x="0" y="0" width="16" height="13" rx="1" fill="var(--red)"/><path d="M1 1l7 6 7-6" fill="none" stroke="#000" stroke-width="1.4"/></svg>info@brisktow.com</div>

  <div class="abs" style="left:112px;top:4459px;font-size:13px;color:var(--muted)">© 2024 Brisk Tow. All Rights Reserved.</div>
  <div class="abs" style="left:863px;top:4459px;font-size:13px;color:var(--muted);word-spacing:4px">Privacy &nbsp;| &nbsp;Terms &nbsp;| &nbsp;Disclaimer</div>
</footer>

</body>
</html>
```